Business Card Design needed - Something Awesome!

Need a business card designed. Company is "Marlowe Advisory" we do consulting and also have sales automation technology.
I'm going to use thick stock or metal, something really nice... I was thinking about a QR Code on the back that would just upload my contact info to the persons contact, etc -

This is a Strategy Company with a tech feel. I'm open to ideas but really want this to be nice!

I need a template that should include:

Name | Position or Title
D: 415.902.3376
www.marloweadvisory.example

I'm going to attach my contact so you can use that one, I need to get this printed.

Target Market(s)

Small to mid size customers, Entrepreneurs etc.

Industry/Entity Type

Consulting, Tech, Private Equity.

Contact Information for Business Card

Name, Phone, Maybe email, URL

Font styles to use
Sans Serif

Colors

Designer to choose only greyscale colors for use in the design.

Requirements
Must have
• Fresh, Clean, stand out from the crowd - will be on thick stock or metal.
Nice to have
• Clean, simple yet impactful.
Should not have
• Not cartoonish

```html
<!DOCTYPE html>
<html lang="en">
<head>
<meta charset="utf-8">
<title>Marlowe Advisory — Business Card</title>
<link rel="stylesheet" href="https://fonts.googleapis.com/css2?family=Arimo:wght@400;700&display=swap">
<style>
  :root {
    --backdrop: #3b3b3d;
    --card: #111112;
    --card-edge: #1c1c1d;
    --silver: #d9d9db;
    --silver-soft: #b4b4b7;
    --rule: #6a6a6d;
    --pattern-dark: #0b0b0c;
    --pattern-mid: #2a2a2c;
    --pattern-light: #3e3e41;
  }
  * { margin: 0; padding: 0; box-sizing: border-box; }
  html, body {
    width: 1200px;
    height: 801px;
    overflow: hidden;
    background: var(--backdrop);
    font-family: "Arimo", Arial, sans-serif;
  }
  .stage {
    position: relative;
    width: 1200px;
    height: 801px;
  }
  .card {
    position: absolute;
    top: 250px;
    width: 525px;
    height: 300px;
    background: var(--card);
    border: 1px solid var(--card-edge);
    border-radius: 3px;
    box-shadow: 0 14px 30px rgba(0,0,0,0.35);
    overflow: hidden;
  }
  .card--front { left: 50px; }
  .card--back { left: 625px; }

  .wordmark {
    color: var(--silver);
    font-weight: 400;
    letter-spacing: 2px;
    text-transform: uppercase;
    display: flex;
    align-items: center;
    gap: 12px;
    white-space: nowrap;
  }
  .wordmark__square {
    width: 18px;
    height: 18px;
    background: var(--silver);
    transform: rotate(45deg);
  }
  .card--front .wordmark {
    position: absolute;
    top: 70px;
    left: 0;
    right: 0;
    justify-content: center;
    font-size: 38px;
  }

  .details {
    position: absolute;
    top: 175px;
    left: 0;
    right: 0;
    display: flex;
    justify-content: center;
    align-items: center;
  }
  .person {
    text-align: right;
    padding-right: 18px;
  }
  .person__name {
    color: var(--silver);
    font-weight: 700;
    font-size: 15px;
    letter-spacing: 0.5px;
    text-transform: uppercase;
  }
  .person__title {
    color: var(--silver-soft);
    font-size: 13px;
    margin-top: 4px;
  }
  .divider {
    width: 1px;
    height: 62px;
    background: var(--rule);
  }
  .contact {
    list-style: none;
    padding-left: 18px;
  }
  .contact__item {
    color: var(--silver-soft);
    font-size: 12.5px;
    display: flex;
    align-items: center;
    gap: 7px;
    line-height: 20px;
  }
  .contact__icon {
    width: 10px;
    height: 10px;
    fill: var(--silver-soft);
    flex: none;
  }

  .pattern {
    position: absolute;
    inset: 0;
    background:
      linear-gradient(135deg, var(--pattern-dark) 0%, var(--pattern-dark) 35%, var(--pattern-mid) 70%, var(--pattern-light) 100%);
  }
  .card--back .wordmark {
    position: absolute;
    top: 160px;
    left: 0;
    right: 0;
    justify-content: center;
    font-size: 34px;
  }
</style>
</head>
<body>
<main class="stage">

  <section class="card card--front" aria-label="Business card front">
    <div class="wordmark">
      <span class="wordmark__square"></span>
      <span class="wordmark__name">Marlowe Advisory</span>
    </div>

    <div class="details">
      <div class="person">
        <p class="person__name">Dorian K. Vale</p>
        <p class="person__title">Founder / CEO</p>
      </div>
      <div class="divider"></div>
      <ul class="contact">
        <li class="contact__item">
          <svg class="contact__icon" viewBox="0 0 10 10" aria-hidden="true"><path d="M2.2 0.5 L3.8 2.6 L2.9 3.6 Q3.9 5.8 6.4 7.1 L7.4 6.2 L9.5 7.8 L8.4 9.5 Q4.5 9.4 2.1 6.9 Q0.4 4.8 0.5 1.6 Z"/></svg>
          415.902.3376
        </li>
        <li class="contact__item">
          <svg class="contact__icon" viewBox="0 0 10 10" aria-hidden="true"><path d="M0.5 2 H9.5 V8.5 H0.5 Z M1.2 2.6 L5 5.6 L8.8 2.6" fill="none" stroke="currentColor"/><path d="M0.5 2 H9.5 L5 5.4 Z"/><path d="M0.5 2.8 L5 6.2 L9.5 2.8 V8.5 H0.5 Z"/></svg>
          info@marloweadvisory.example
        </li>
        <li class="contact__item">
          <svg class="contact__icon" viewBox="0 0 10 10" aria-hidden="true"><circle cx="5" cy="5" r="4.4" fill="none" stroke="#b4b4b7" stroke-width="1"/><ellipse cx="5" cy="5" rx="1.8" ry="4.4" fill="none" stroke="#b4b4b7" stroke-width="0.8"/><path d="M0.6 5 H9.4" stroke="#b4b4b7" stroke-width="0.8"/></svg>
          www.marloweadvisory.example
        </li>
      </ul>
    </div>
  </section>

  <section class="card card--back" aria-label="Business card back">
    <div class="pattern" role="img" aria-label="Gloss tiled square pattern in black and charcoal greys"></div>
    <div class="wordmark">
      <span class="wordmark__square"></span>
      <span class="wordmark__name">Marlowe Advisory</span>
    </div>
  </section>

</main>
</body>
</html>
```